WordPress Design (redesign) and Coding for Funeral Consulting Services & mobile app

I need an attractive SEO friendly WordPress design.

Incorporating all of the latest design standards in a graceful and appealing way. I'd like to see CTA's for for funeral consulting services. People should be able to purchase my consulting services directly from the website so I'd like to see nice buttons.

Funeral Consulting Services are the main topic for this website.

I also have an iOS app called Velomarque in the iOS Appvault Shelf. I want buttons and CTAs so that users can download the app right to their iOS device(s). Make this a secondary focus.

I want more of a mobile focus as that is where I expect the most traffic. Mobile users like to act quickly and they also like to scroll if their interest is captured so I want the design to reflect that.

End to end design
Large Creative Typography for increased mobile searchers.
attractive CTA’s
RGB Vivid / Bright Colors that match our logo
A menu that is easy to find and use on mobile devices
button(s) for iOS app download.

the current website is www.velomarque-example.com This website was a placeholder.
Updates

I'd need users to fill out a survey so that I may collect information from them to better provide service to them.

reference websites: Quillvant.com & Torbex.com for website design inspiratioin. reference Harnwick.com for blog

Target Market(s)

18-35 year old mobile users

Industry/Entity Type

Consulting

Coding

Coded - Design and coding required

Font styles to use
Sans Serif

Colors
fbee3d
000000
ffffff
cbcbcb
fefdec

Requirements
Must have
• iOS app logo and iOS app logo colors should have its own area/page
• CTA's for consulting services and app download. Main topic
• reviews (testimonials)
• Video area
• end to end design
• creative typography
Nice to have
• a beautiful blog page that blends well with the design
Should not have
• Any imagery related to funerals or burials.

```html
<!DOCTYPE html>
<html lang="en">
<head>
<meta charset="utf-8">
<title>Velomarque – Funeral Consulting Services</title>
<link href="https://fonts.googleapis.com/css2?family=Lato:wght@400;700&display=swap" rel="stylesheet">
<style>
  :root {
    --yellow: #fbee3d;
    --black: #000000;
    --white: #ffffff;
    --grey: #cbcbcb;
    --cream: #fefdec;
    --ink: #1a1a1a;
    --body: #333333;
  }
  * { box-sizing: border-box; margin: 0; padding: 0; }
  html, body { width: 1200px; height: 3209px; overflow: hidden; }
  body { font-family: "Lato", Arial, sans-serif; color: var(--ink); background: var(--white); position: relative; }
  .abs { position: absolute; }
  .btn {
    position: absolute; background: var(--yellow); color: var(--black);
    display: flex; align-items: center; justify-content: center;
    font-size: 15px; text-decoration: none; box-shadow: 0 2px 3px rgba(0,0,0,.12);
  }

  /* Header */
  .site-header { left: 0; top: 0; width: 1200px; height: 113px; background: var(--white); }
  .brand { left: 96px; top: 30px; display: flex; align-items: center; gap: 12px; }
  .brand-mark { width: 22px; height: 22px; border-radius: 50%; background: var(--yellow); }
  .brand-name { font-size: 36px; font-weight: 700; color: var(--black); }
  .main-nav { right: 92px; top: 52px; display: flex; gap: 30px; font-size: 15px; }
  .main-nav a { color: var(--black); text-decoration: none; position: relative; }
  .main-nav a.active::after { content: ""; position: absolute; left: -4px; right: -4px; top: 54px; height: 4px; background: var(--yellow); }

  /* Hero */
  .hero { left: 0; top: 113px; width: 1200px; height: 550px; background: linear-gradient(100deg, #c9b6a6 0%, #e9e4de 35%, #d8dde0 60%, #e7e2da 100%); }
  .hero-banner { left: 635px; top: 274px; width: 565px; height: 133px; }
  .hero-title { left: 692px; top: 290px; text-align: right; width: 410px; }
  .hero-title .l1 { font-size: 44px; display: block; }
  .hero-title .l2 { font-size: 31px; display: block; margin-top: 2px; }
  .hero-dots { left: 566px; top: 489px; display: flex; gap: 10px; }
  .hero-dots span { width: 9px; height: 9px; border-radius: 50%; background: rgba(255,255,255,.7); }

  /* Intro */
  .intro-text { left: 150px; top: 712px; width: 900px; text-align: center; font-size: 21px; line-height: 30px; color: var(--black); }
  .intro-btn { left: 456px; top: 898px; width: 288px; height: 39px; font-size: 19px; }

  /* Advice */
  .advice { left: 0; top: 984px; width: 1200px; height: 556px; background: var(--cream); }
  .advice p { position: absolute; font-size: 13px; line-height: 21px; text-align: justify; color: var(--black); }
  .phone { border-radius: 38px; background: linear-gradient(180deg, #2a2a2a, #0c0c0c); }
  .phone-screen { position: absolute; left: 14px; right: 14px; top: 68px; bottom: 78px; border-radius: 4px; }

  /* Video */
  .video { left: 0; top: 1540px; width: 1200px; height: 488px; background: linear-gradient(110deg, #9ea4ab 0%, #c9cdd1 40%, #b4b9be 70%, #d3d5d7 100%); }
  .video-frame { left: 143px; top: 1608px; width: 475px; height: 351px; background: var(--white); display: flex; align-items: center; justify-content: center; gap: 14px; }
  .video-frame .name { font-size: 38px; font-weight: 700; color: var(--black); }
  .play { width: 54px; height: 54px; border-radius: 50%; background: var(--black); display: flex; align-items: center; justify-content: center; }
  .video-quote { left: 669px; top: 1670px; width: 386px; font-size: 22px; line-height: 27px; text-align: justify; color: var(--black); }

  /* App */
  .app-title { left: 483px; top: 2130px; font-size: 31px; color: var(--black); }
  .app-text { left: 483px; top: 2184px; width: 545px; font-size: 15px; line-height: 21px; color: var(--body); }
  .reviews-title { left: 487px; top: 2338px; font-size: 24px; color: var(--black); }
  .stars { left: 484px; top: 2386px; display: flex; gap: 14px; }
  .review-text { left: 478px; top: 2428px; width: 550px; font-size: 14px; line-height: 20px; color: var(--body); }

  /* Blog */
  .blog { left: 0; top: 2635px; width: 1200px; height: 388px; background: var(--yellow); }
  .blog-title { left: 0; width: 1200px; top: 2676px; text-align: center; font-size: 24px; color: var(--black); }
  .post { position: absolute; top: 2738px; width: 267px; height: 220px; background: var(--white); }
  .post .date { position: absolute; left: 10px; top: 10px; width: 48px; height: 57px; background: var(--black); color: var(--white); text-align: center; }
  .post .date b { display: block; font-size: 22px; font-weight: 700; margin-top: 6px; }
  .post .date span { font-size: 12px; }
  .post h3 { position: absolute; left: 72px; top: 32px; width: 180px; font-size: 17px; font-weight: 400; line-height: 20px; color: var(--black); }
  .post p { position: absolute; left: 16px; top: 88px; width: 236px; font-size: 11.5px; line-height: 19px; text-align: justify; color: var(--body); }

  /* Footer */
  .footer-mark { left: 571px; top: 2993px; width: 58px; height: 58px; border-radius: 50%; background: var(--yellow); border: 5px solid var(--black); }
  .footer-nav { left: 0; width: 1200px; top: 3072px; display: flex; justify-content: center; gap: 26px; font-size: 15px; }
  .footer-nav a { color: var(--black); text-decoration: none; }
  .social { left: 0; width: 1200px; top: 3112px; display: flex; justify-content: center; align-items: center; gap: 18px; font-size: 12px; font-weight: 700; }
  .social a { color: var(--black); text-decoration: none; width: 44px; height: 44px; display: flex; align-items: center; justify-content: center; }
  .social a.on { background: var(--yellow); border-radius: 50%; width: 50px; height: 50px; }
  .copyright { left: 0; width: 1200px; top: 3173px; text-align: center; font-size: 12px; color: var(--body); }
</style>
</head>
<body>

<header class="site-header abs">
  <div class="brand abs"><span class="brand-mark"></span><span class="brand-name">Velomarque</span></div>
  <nav class="main-nav abs">
    <a class="active" href="#">Home</a><a href="#">About Us</a><a href="#">App Reviews</a><a href="#">Video</a><a href="#">Blog</a><a href="#">Contact Us</a>
  </nav>
</header>

<section class="hero abs" role="img" aria-label="Photo of a family gathered together, comforting one another"></section>
<svg class="hero-banner abs" viewBox="0 0 565 133" aria-hidden="true"><polygon points="0,0 565,0 565,133 44,133" fill="#fbee3d"/></svg>
<h1 class="hero-title abs"><span class="l1">We provide Funeral</span><span class="l2">Consulting Services.</span></h1>
<div class="hero-dots abs"><span></span><span></span><span></span></div>

<p class="intro-text abs">Funerals are expensive. Having to finance one suddenly can be a burden to many families, especially those that are uninsured or unprepared. Not coincidently, there is often a windfall of money at this time, in the form of donations, family contributions, and life insurance proceeds. Families tend to consider that money 'going away' funds. The funeral industry wants to pressure you into spending your last dollar on that event</p>
<a class="btn intro-btn" href="#">DON'T Throw Money Away</a>

<section class="advice abs">
  <p style="left:156px;top:96px;width:265px;">The fact is, life insurance was never intended to be fully used on a fancy funeral, but rather as a hedge against disaster for the survivors.</p>
  <p style="left:156px;top:252px;width:265px;">A funeral consultant is someone who, on their own, goes out and does all the things related to making funeral arrangements. However we do so with your budget and your ideals in mind. We represent you as your spokesperson and friend during this tough time.</p>
  <p style="left:473px;top:96px;width:267px;">The first step in funeral planning, particularly if you find yourself at-need, is to get a friend by your side. This should be someone who is somewhat removed from the deceased, so the friend's emotions will not be a factor. It should also be someone whose judgement you trust and, preferably, someone who has been through the arrangement process in the recent past. This friend should be someone who has the strength of character to say 'NO' or at least 'Not YET', to keep you from being pressured into hasty, expensive financial decisions.</p>
  <div class="phone abs" style="left:796px;top:34px;width:231px;height:488px;" role="img" aria-label="Smartphone showing the Velomarque app sign-in screen">
    <div class="phone-screen" style="background:linear-gradient(180deg,#e8edd0 0%,#c4cf8a 55%,#6f8a3a 100%);"></div>
  </div>
</section>
<a class="btn" href="#" style="left:156px;top:1172px;width:150px;height:32px;font-size:13px;">SAVE MONEY NOW</a>
<a class="btn" href="#" style="left:156px;top:1395px;width:124px;height:34px;font-size:13px;">Get Help ASAP</a>
<a class="btn" href="#" style="left:473px;top:1382px;width:148px;height:33px;font-size:13px;">Save Money Today</a>

<section class="video abs" role="img" aria-label="Soft background photo of a support group meeting"></section>
<div class="video-frame abs">
  <span class="name">Velomarque</span>
  <span class="play"><svg width="22" height="24" viewBox="0 0 22 24"><polygon points="2,0 22,12 2,24" fill="#fff"/></svg></span>
</div>
<p class="video-quote abs">In a survey of several thousand funeral directors, in response to the question Why would you say funerals cost so much?, over 85% replied "Emotional overspending by the family."</p>
<a class="btn" href="#" style="left:669px;top:1825px;width:150px;height:36px;">Get help now</a>

<div class="phone abs" style="left:184px;top:2088px;width:229px;height:490px;" role="img" aria-label="Smartphone showing the app newsfeed with a friend's post and photo">
  <div class="phone-screen" style="background:linear-gradient(180deg,#ffffff 0%,#f2f2f2 45%,#c9b3a5 70%,#f2f2f2 100%);"></div>
</div>
<h2 class="app-title abs">Our App</h2>
<p class="app-text abs">Sed ut perspiciatis unde omnis iste natus error sit voluptatem accusantium doloremque laudantium, totam rem aperiam, eaque ipsa quae ab illo inventore veritatis et quasi architecto beatae vitae dicta sunt explicabo.</p>
<a class="btn" href="#" style="left:483px;top:2270px;width:150px;height:36px;">Download&nbsp;&nbsp;<svg width="14" height="14" viewBox="0 0 14 14"><path d="M7 1v8M3.5 5.5L7 9l3.5-3.5M1 12.5h12" stroke="#000" stroke-width="2" fill="none"/></svg></a>
<h3 class="reviews-title abs">App Reviews</h3>
<div class="stars abs">
  <svg width="24" height="24" viewBox="0 0 24 24"><polygon points="12,1 15,9 23,9 17,14 19,23 12,18 5,23 7,14 1,9 9,9" fill="#fbee3d" stroke="#d8cc20"/></svg>
  <svg width="24" height="24" viewBox="0 0 24 24"><polygon points="12,1 15,9 23,9 17,14 19,23 12,18 5,23 7,14 1,9 9,9" fill="#fbee3d" stroke="#d8cc20"/></svg>
  <svg width="24" height="24" viewBox="0 0 24 24"><polygon points="12,1 15,9 23,9 17,14 19,23 12,18 5,23 7,14 1,9 9,9" fill="#fbee3d" stroke="#d8cc20"/></svg>
  <svg width="24" height="24" viewBox="0 0 24 24"><polygon points="12,1 15,9 23,9 17,14 19,23 12,18 5,23 7,14 1,9 9,9" fill="#fbee3d" stroke="#d8cc20"/></svg>
  <svg width="24" height="24" viewBox="0 0 24 24"><polygon points="12,1 15,9 23,9 17,14 19,23 12,18 5,23 7,14 1,9 9,9" fill="#fbee3d" stroke="#d8cc20"/></svg>
</div>
<p class="review-text abs">"Duis aute irure dolor in reprehenderit in voluptate velit esse cillum dolore eu fugiat nulla pariatur. Excepteur sint occaecat cupidatat non proident, sunt in culpa qui officia deserunt mollit anim id est laborum."</p>
<a class="btn" href="#" style="left:475px;top:2503px;width:88px;height:25px;font-size:12px;">Read more</a>

<section class="blog abs"></section>
<h2 class="blog-title abs">Blog</h2>
<article class="post" style="left:154px;">
  <div class="date"><b>01</b><span>Dec</span></div>
  <h3>Finibus Bonorum et Malorum</h3>
  <p>Sed ut perspiciatis unde omnis iste natus error sit voluptatem accusantium doloremque laudantium, totam rem aperiam, eaque ipsa quae ab illo inventore veritatis et quasi architecto beatae vitae .</p>
</article>
<article class="post" style="left:466px;">
  <div class="date"><b>01</b><span>Dec</span></div>
  <h3>Finibus Bonorum et Malorum</h3>
  <p>Sed ut perspiciatis unde omnis iste natus error sit voluptatem accusantium doloremque laudantium, totam rem aperiam, eaque ipsa quae ab illo inventore veritatis et quasi architecto beatae vitae .</p>
</article>
<article class="post" style="left:779px;">
  <div class="date"><b>01</b><span>Dec</span></div>
  <h3>Finibus Bonorum et Malorum</h3>
  <p>Sed ut perspiciatis unde omnis iste natus error sit voluptatem accusantium doloremque laudantium, totam rem aperiam, eaque ipsa quae ab illo inventore veritatis et quasi architecto beatae vitae .</p>
</article>

<footer>
  <div class="footer-mark abs"></div>
  <nav class="footer-nav abs">
    <a href="#">Home</a><a href="#">About Us</a><a href="#">App Reviews</a><a href="#">Video</a><a href="#">Blog</a><a href="#">Contact Us</a>
  </nav>
  <div class="social abs">
    <a href="#">Facet</a><a class="on" href="#">Lenscircle</a><a href="#">Chirper</a><a href="#">Plusring</a>
  </div>
  <p class="copyright abs">Copyrights © 2017 - All Rights Reserved</p>
</footer>

</body>
</html>
```